Real Estate Webpage Design

We have an existing website: ferndaleestatecollective.com.au
We focus customised service mainly on Property Management and second-hand property sales.
We are not entirely happy about the current design and layout can stay roughly the same as the back end coding is linked to a CRM system.
We would like to see the design are more reachable to our clients and appearing.
Please check our Website Design Draft for more details.

Industry/Entity Type

Real estate Agency

Number of Pages Required

5+ page

Font styles to use
Sans Serif

Colors

Designer to choose colors to be used in the design.

```html
<!DOCTYPE html>
<html lang="en">
<head>
<meta charset="utf-8">
<title>Ferndale Estate Collective</title>
<link href="https://fonts.googleapis.com/css2?family=Montserrat:wght@400;600;700;800&family=Open+Sans:wght@400;600&display=swap" rel="stylesheet">
<style>
:root{
  --navy:#1f2a3c;
  --navy-deep:#18212f;
  --gold:#e8b23a;
  --gold-dark:#c9962a;
  --ink:#2b2f36;
  --muted:#7a808a;
  --light:#f4f5f7;
  --grey:#eceef1;
  --white:#ffffff;
  --line:#dfe2e6;
}
*{margin:0;padding:0;box-sizing:border-box}
html,body{width:1200px;height:3476px;overflow:hidden;background:var(--white)}
body{font-family:"Open Sans",Arial,sans-serif;color:var(--ink);position:relative}
h1,h2,h3,h4,.brand,.btn,.nav a{font-family:"Montserrat",Arial,sans-serif}
.btn{display:inline-block;background:var(--gold);color:var(--navy);font-size:13px;font-weight:700;padding:10px 22px;border-radius:3px;text-transform:uppercase;letter-spacing:.5px}

/* Header & hero */
.hero{position:absolute;left:0;top:0;width:1200px;height:640px;background:linear-gradient(180deg,#6f9cc9 0%,#9dbbd9 38%,#cfd6dc 62%,#8c9299 100%)}
.site-header{position:absolute;left:0;top:0;width:1200px;height:80px;display:flex;align-items:center;justify-content:space-between;padding:0 60px;background:rgba(20,30,45,.25)}
.brand{display:flex;align-items:center;gap:10px;color:var(--white);font-weight:700;font-size:24px}
.brand .mark{width:26px;height:26px;background:var(--gold)}
.brand small{display:block;font-size:10px;font-weight:600;letter-spacing:1px}
.nav{display:flex;gap:26px}
.nav a{color:var(--white);text-decoration:none;font-size:14px;font-weight:600;padding-bottom:6px}
.nav a.active{border-bottom:2px solid var(--gold)}
.hero-title{position:absolute;top:150px;width:1200px;text-align:center;color:var(--white);font-size:34px;font-weight:800;letter-spacing:1px}
.hero-cta{position:absolute;top:210px;left:0;width:1200px;text-align:center}
.services{position:absolute;top:600px;left:120px;width:960px;display:flex;justify-content:space-between}
.service{width:280px;height:90px;background:var(--white);box-shadow:0 6px 18px rgba(0,0,0,.12);display:flex;align-items:center;gap:18px;padding:0 22px;font-family:"Montserrat",sans-serif;font-weight:700;font-size:14px;color:var(--navy);text-transform:uppercase;line-height:1.35}
.service .icon{width:50px;height:50px;flex:none;background:var(--navy);display:flex;align-items:center;justify-content:center}

/* About */
.about{position:absolute;top:730px;left:120px;width:960px;height:440px}
.about-photo{position:absolute;left:0;top:0;width:480px;height:440px;background:linear-gradient(160deg,#b9c6d4,#7b8794 60%,#4d5661)}
.about-text{position:absolute;left:540px;top:20px;width:420px}
.about-text h2{font-size:24px;font-weight:800;color:var(--navy);line-height:1.3;margin-bottom:24px}
.about-text p{font-size:13px;line-height:1.75;color:var(--muted);margin-bottom:16px}

/* Listings */
.section-title{position:absolute;width:1200px;text-align:center;font-size:24px;font-weight:800;color:var(--navy)}
.tabs{position:absolute;top:1262px;left:0;width:1200px;display:flex;justify-content:center;gap:14px}
.tab{font-size:12px;border:1px solid var(--line);padding:7px 16px;background:var(--white);color:var(--ink)}
.tab.active{background:var(--gold);border-color:var(--gold);color:var(--navy);font-weight:600}
.listings{position:absolute;top:1320px;left:135px;width:930px;display:flex;justify-content:space-between}
.card{width:290px;background:var(--white);box-shadow:0 4px 14px rgba(0,0,0,.1)}
.card .photo{height:190px}
.card .body{padding:16px 18px 14px}
.card h3{font-size:15px;font-weight:800;color:var(--navy)}
.card .addr{font-size:11px;color:var(--muted);margin:3px 0 10px}
.card .price{font-family:"Montserrat",sans-serif;font-size:22px;font-weight:800;color:var(--gold-dark)}
.card .insp{font-size:11px;color:var(--muted);margin:8px 0 12px;line-height:1.5}
.card .meta{display:flex;align-items:center;justify-content:space-between;border-top:1px solid var(--line);padding-top:10px;font-size:11px;color:var(--muted)}
.card .meta span.tag{background:var(--gold);color:var(--navy);font-weight:700;font-size:10px;padding:4px 8px}
.arrow{position:absolute;font-family:"Montserrat",sans-serif;font-size:30px;color:var(--navy)}

/* Why choose us */
.why{position:absolute;top:1790px;left:0;width:1200px;height:500px;background:var(--grey)}
.why .section-title{top:40px}
.feature{position:absolute;width:300px;display:flex;gap:16px}
.feature .icon{width:44px;height:44px;flex:none;background:var(--gold);display:flex;align-items:center;justify-content:center}
.feature h4{font-size:14px;font-weight:800;color:var(--navy);margin-bottom:6px;text-transform:uppercase}
.feature p{font-size:11px;line-height:1.6;color:var(--muted)}
.why-emblem{position:absolute;left:480px;top:140px;width:240px;height:240px}

/* Featured */
.featured-photo{position:absolute;top:2380px;left:120px;width:960px;height:420px;background:linear-gradient(180deg,#2c4c6e 0%,#4e6a86 45%,#8a7b63 75%,#3a3f38 100%)}
.featured-card{position:absolute;top:2440px;left:140px;width:280px;background:var(--white);padding:20px 22px;box-shadow:0 6px 18px rgba(0,0,0,.2)}
.featured-card h3{font-size:15px;font-weight:800;color:var(--navy)}
.featured-card .addr{font-size:11px;color:var(--muted);margin:4px 0 12px}
.featured-card .insp{font-size:11px;color:var(--muted);line-height:1.6;margin-bottom:14px}
.slide-btn{position:absolute;width:30px;height:30px;background:var(--navy);color:var(--white);font-size:16px;display:flex;align-items:center;justify-content:center}

/* Testimonials */
.testimonials{position:absolute;top:2860px;left:0;width:1200px;height:340px;background:var(--light)}
.quotes{position:absolute;top:100px;left:135px;width:930px;display:flex;justify-content:space-between}
.quote{width:290px;text-align:center}
.quote .box{background:var(--white);padding:22px 26px;box-shadow:0 3px 10px rgba(0,0,0,.06)}
.quote .mark{font-family:"Montserrat",sans-serif;font-size:40px;color:var(--gold);line-height:.8}
.quote p{font-size:11px;line-height:1.65;color:var(--muted);margin-top:8px}
.quote h4{font-size:12px;font-weight:800;color:var(--navy);margin-top:16px}
.quote small{font-size:10px;color:var(--muted)}

/* Footer */
.site-footer{position:absolute;top:3200px;left:0;width:1200px;height:276px;background:var(--navy)}
.site-footer .brand{position:absolute;left:120px;top:60px}
.social{position:absolute;right:120px;top:66px;display:flex;align-items:center;gap:10px;color:var(--white);font-size:13px}
.social i{display:block;width:24px;height:24px;border-radius:3px}
.footer-line{position:absolute;left:120px;top:150px;width:960px;height:1px;background:rgba(255,255,255,.15)}
.footer-links{position:absolute;left:120px;top:230px;display:flex;gap:22px;font-size:11px;color:#c9ced6}
.copyright{position:absolute;right:120px;top:230px;font-size:11px;color:#c9ced6}
</style>
</head>
<body>

<section class="hero" role="img" aria-label="Photo of a large white two-storey family home under a blue sky"></section>
<header class="site-header">
  <div class="brand"><span class="mark"></span><span>Ferndale<small>ESTATE COLLECTIVE</small></span></div>
  <nav class="nav">
    <a class="active">Home</a><a>About Us</a><a>Leasing</a><a>Buy</a><a>Sell</a><a>Our Team</a><a>Blog</a><a>Contact Us</a>
  </nav>
</header>
<h1 class="hero-title">WELCOME TO FERNDALE ESTATE COLLECTIVE</h1>
<div class="hero-cta"><span class="btn">Read More</span></div>

<div class="services">
  <div class="service"><span class="icon"><svg width="26" height="26" viewBox="0 0 26 26" fill="none" stroke="#e8b23a" stroke-width="2.5"><circle cx="11" cy="11" r="7"/><line x1="16" y1="16" x2="23" y2="23"/></svg></span>Search available properties</div>
  <div class="service"><span class="icon"><svg width="26" height="26" viewBox="0 0 26 26" fill="none" stroke="#e8b23a" stroke-width="2.5"><rect x="3" y="7" width="20" height="13" rx="2"/><circle cx="13" cy="13.5" r="3"/></svg></span>Rent collection</div>
  <div class="service"><span class="icon"><svg width="26" height="26" viewBox="0 0 26 26" fill="none" stroke="#e8b23a" stroke-width="2.5"><path d="M3 12 L13 4 L23 12"/><rect x="6" y="12" width="14" height="10"/></svg></span>Property management</div>
</div>

<section class="about">
  <div class="about-photo" role="img" aria-label="Photo of a modern apartment building with glass balconies"></div>
  <div class="about-text">
    <h2>FERNDALE – ROOTED IN<br>“THE HOME”</h2>
    <p>Ferndale is all about “the home, the house”. Buying a property is one of the most expensive and important assets for people. Ferndale is a real estate company located in Gungahlin, Canberra.</p>
    <p>Being a portfolio sales agent and property manager, coupled with our high-profile international real estate experience, Ferndale is considered a market leader as the cutting edge with deep industry knowledge, ranging from landlord-tenant relationships, residential purchases.</p>
    <span class="btn">Read More</span>
  </div>
</section>

<h2 class="section-title" style="top:1210px">THIS MONTH AT FERNDALE ESTATE COLLECTIVE</h2>
<div class="tabs"><span class="tab active">For Sale</span><span class="tab">For Lease</span><span class="tab">Open Today</span><span class="tab">Sold</span><span class="tab">Leased</span></div>
<span class="arrow" style="left:70px;top:1470px">‹</span>
<span class="arrow" style="right:70px;top:1470px">›</span>
<div class="listings">
  <article class="card">
    <div class="photo" role="img" aria-label="Photo of a home with a pool at dusk" style="background:linear-gradient(180deg,#3f6fae,#8bb0d6 60%,#5b7c8f)"></div>
    <div class="body"><h3>GUNGAHLIN</h3><p class="addr">Level 6/17 Wattle Crescent Gungahlin</p><div class="price">$500,000+</div><p class="insp">Next Inspection<br>Sat, 21st May 09:30 AM – 10:00 AM</p><div class="meta"><span>🛏 3 &nbsp;🛁 2 &nbsp;🚗 2</span><span>2000 sq m</span><span class="tag">VIEW DETAILS</span></div></div>
  </article>
  <article class="card">
    <div class="photo" role="img" aria-label="Photo of a modern apartment block" style="background:linear-gradient(180deg,#7fa8d1,#c7ccd1 55%,#7d848c)"></div>
    <div class="body"><h3>BELCONNEN</h3><p class="addr">2 Banksia Lane Belconnen</p><div class="price">$300,000+</div><p class="insp">Next Inspection<br>Sat, 21st May 09:30 AM – 10:00 AM</p><div class="meta"><span>🛏 2 &nbsp;🛁 1 &nbsp;🚗 1</span><span>2000 sq m</span><span class="tag">VIEW DETAILS</span></div></div>
  </article>
  <article class="card">
    <div class="photo" role="img" aria-label="Photo of a large family house at twilight" style="background:linear-gradient(180deg,#4a6d9c,#a8b5c4 55%,#6a6458)"></div>
    <div class="body"><h3>GUNGAHLIN</h3><p class="addr">Level 6/17 Wattle Crescent Gungahlin</p><div class="price">$500,000+</div><p class="insp">Next Inspection<br>Sat, 21st May 09:30 AM – 10:00 AM</p><div class="meta"><span>🛏 4 &nbsp;🛁 2 &nbsp;🚗 2</span><span>2000 sq m</span><span class="tag">VIEW DETAILS</span></div></div>
  </article>
</div>

<section class="why">
  <h2 class="section-title">WHY CHOOSE US</h2>
  <div class="feature" style="left:120px;top:150px"><span class="icon"><svg width="22" height="22" viewBox="0 0 22 22" fill="none" stroke="#1f2a3c" stroke-width="2.2"><path d="M11 2 L19 5 V11 C19 16 11 20 11 20 C11 20 3 16 3 11 V5 Z"/></svg></span><div><h4>30-Day Lease Guarantee</h4><p>Lorem Ipsum is simply dummy text of the printing and typesetting industry. Lorem.</p></div></div>
  <div class="feature" style="left:120px;top:290px"><span class="icon"><svg width="22" height="22" viewBox="0 0 22 22" fill="none" stroke="#1f2a3c" stroke-width="2.2"><path d="M4 11 L9 16 L18 6"/></svg></span><div><h4>Results Promise</h4><p>Lorem Ipsum is simply dummy text of the printing and typesetting industry. Lorem.</p></div></div>
  <svg class="why-emblem" viewBox="0 0 240 240"><rect x="50" y="50" width="140" height="140" fill="none" stroke="#e8b23a" stroke-width="22" transform="rotate(45 120 120)"/><rect x="95" y="95" width="50" height="50" fill="#1f2a3c"/></svg>
  <div class="feature" style="left:780px;top:150px"><span class="icon"><svg width="22" height="22" viewBox="0 0 22 22" fill="none" stroke="#1f2a3c" stroke-width="2.2"><path d="M4 13 L8 9 L12 13 L18 6"/></svg></span><div><h4>Satisfaction</h4><p>Lorem Ipsum is simply dummy text of the printing and typesetting industry. Lorem.</p></div></div>
  <div class="feature" style="left:780px;top:290px"><span class="icon"><svg width="22" height="22" viewBox="0 0 22 22" fill="none" stroke="#1f2a3c" stroke-width="2.2"><circle cx="11" cy="11" r="8"/><circle cx="11" cy="11" r="3"/></svg></span><div><h4>Support</h4><p>Lorem Ipsum is simply dummy text of the printing and typesetting industry. Lorem.</p></div></div>
</section>

<h2 class="section-title" style="top:2330px">FEATURED PROPERTY</h2>
<div class="featured-photo" role="img" aria-label="Photo of a contemporary house lit up at dusk"></div>
<div class="featured-card">
  <h3>GUNGAHLIN</h3>
  <p class="addr">Level 6/17 Wattle Crescent Gungahlin</p>
  <p class="insp">Next Inspection<br>Sat, 21st May 09:30 AM – 10:00 AM</p>
  <span class="btn" style="font-size:10px;padding:6px 12px">View Details</span>
</div>
<span class="slide-btn" style="left:108px;top:2575px">‹</span>
<span class="slide-btn" style="left:1062px;top:2575px">›</span>

<section class="testimonials">
  <h2 class="section-title" style="top:36px">TESTIMONIALS</h2>
  <span class="arrow" style="left:80px;top:160px">‹</span>
  <span class="arrow" style="right:80px;top:160px">›</span>
  <div class="quotes">
    <div class="quote"><div class="box"><div class="mark">“</div><p>There are many variations of passages of Lorem Ipsum available, but the majority have suffered alteration in some form, by injected humour, or randomised words which don't look even slightly believable.</p></div><h4>RICHARD</h4><small>England</small></div>
    <div class="quote"><div class="box"><div class="mark">“</div><p>There are many variations of passages of Lorem Ipsum available, but the majority have suffered alteration in some form, by injected humour, or randomised words which don't look even slightly believable.</p></div><h4>SMITH</h4><small>England</small></div>
    <div class="quote"><div class="box"><div class="mark">“</div><p>There are many variations of passages of Lorem Ipsum available, but the majority have suffered alteration in some form, by injected humour, or randomised words which don't look even slightly believable.</p></div><h4>STANLY</h4><small>England</small></div>
  </div>
</section>

<footer class="site-footer">
  <div class="brand"><span class="mark"></span><span>Ferndale<small>ESTATE COLLECTIVE</small></span></div>
  <div class="social">Follow us <i style="background:#3b5a99"></i><i style="background:#3aa4e0"></i><i style="background:#d6463a"></i><i style="background:#b53a8c"></i><i style="background:#d0312d"></i></div>
  <div class="footer-line"></div>
  <div class="footer-links"><span>Contact Us</span><span>Privacy</span><span>Complaint Handling &amp; Dispute Resolution</span><span>Due Diligence Checklist</span><span>Sitemap</span></div>
  <div class="copyright">Copyright © 2024 All Rights Reserved</div>
</footer>

</body>
</html>
```